Update the A4 Specials Page for Restaurant/Cafe

Provide a MINIMALIST attractive Specials page we can print weekly for our food and drink specials to give to our guests. Final design is to be provided in WORD Document so it can be easily edited by Manager. Should be black text and MINIMALIST to minimise ink usage as we print hundreds a week. We have UPLOADED the existing page as a template for you to update. Maybe logo can stay, see what you think. Or delete it and do something else. Keep it simple. Choose a good FONT. Could be a little playful with a cocktail ICON or something. Our existing menus can be seen at www.saltmeadowcafe.com.au and they are using font Alegreya. Please note we are unable to provide any feedback to designers, however we really do appreciate your time if you are submitting a design. Thank you for your participation.

```html
<!DOCTYPE html>
<html lang="en">
<head>
<meta charset="utf-8">
<title>Weekly Specials – Salt Meadow Cafe</title>
<link href="https://fonts.googleapis.com/css2?family=Ultra&family=Montserrat:wght@500;600;700&display=swap" rel="stylesheet">
<style>
  :root {
    --surround: #c8c8ca;
    --paper: #ffffff;
    --ink: #111111;
    --rule: #222222;
    --icon-tint: #eeeff0;
  }
  * { margin: 0; padding: 0; box-sizing: border-box; }
  html, body { width: 920px; height: 1200px; overflow: hidden; }
  body { background: var(--surround); position: relative; font-family: "Montserrat", sans-serif; color: var(--ink); }

  .page { position: absolute; left: 118px; top: 117px; width: 683px; height: 966px; background: var(--paper); }
  .page-frame { position: absolute; left: 148px; top: 145px; width: 623px; height: 910px; }

  .title {
    position: absolute; left: 0; width: 920px; top: 186px; text-align: center;
    font-family: "Ultra", "Rockwell Extra Bold", Georgia, serif;
    font-weight: 400; font-size: 38px; letter-spacing: 1px; line-height: 50px; color: var(--ink);
  }

  .banner { position: absolute; left: 306px; width: 307px; height: 30px; }
  .banner svg { position: absolute; inset: 0; }
  .banner-label {
    position: relative; display: block; text-align: center;
    font-weight: 500; font-size: 21px; line-height: 30px; letter-spacing: 0.3px; color: var(--ink);
  }

  .line {
    position: absolute; left: 0; width: 920px; text-align: center;
    font-weight: 600; font-size: 13px; line-height: 16px;
  }
  .line.caps { text-transform: uppercase; }
  .price {
    position: absolute; left: 0; width: 920px; text-align: center;
    color: var(--ink); font-weight: 700; font-size: 23px; line-height: 28px;
  }

  .icon { position: absolute; width: 88px; border-radius: 8px; background: var(--icon-tint); }
  .icon.left { left: 182px; }
  .icon.right { left: 648px; }

  .brand-block {
    position: absolute; left: 365px; top: 997px; width: 190px; height: 86px;
    background: var(--paper); border: 1.5px solid var(--rule); border-bottom: none;
    display: flex; flex-direction: column; align-items: center; justify-content: center;
    font-weight: 700; font-size: 20px; line-height: 24px; letter-spacing: 1px; text-align: center; color: var(--ink);
  }
</style>
</head>
<body>
  <div class="page"></div>
  <svg class="page-frame" viewBox="0 0 623 910" width="623" height="910" aria-hidden="true">
    <rect x="1" y="1" width="621" height="908" fill="none" stroke="var(--rule)" stroke-width="1.5" stroke-dasharray="9 7"/>
  </svg>

  <h1 class="title">WEEKLY SPECIALS</h1>

  <!-- Chicken filo -->
  <div class="icon left" style="top:287px;height:90px" role="img" aria-label="Faint line icon of a chicken"></div>
  <div class="icon right" style="top:287px;height:90px" role="img" aria-label="Faint line icon of a chicken"></div>
  <div class="banner" style="top:284px">
    <svg viewBox="0 0 307 30" width="307" height="30" aria-hidden="true"><polygon points="1,1 306,1 291,15 306,29 1,29 16,15" fill="none" stroke="var(--rule)" stroke-width="1.5"/></svg>
    <span class="banner-label">CHICKEN FILO</span>
  </div>
  <p class="line" style="top:323px">Creamy Chicken with Pinenuts,</p>
  <p class="line" style="top:339px">wrapped in Filo Pastry.</p>
  <p class="line" style="top:365px">Served with Side Salad &amp; Zulu Sauce</p>
  <p class="price" style="top:388px">$24</p>

  <!-- Minestrone soup -->
  <div class="icon left" style="top:453px;height:88px" role="img" aria-label="Faint line icon of a steaming soup bowl"></div>
  <div class="icon right" style="top:453px;height:88px" role="img" aria-label="Faint line icon of a steaming soup bowl"></div>
  <div class="banner" style="top:458px">
    <svg viewBox="0 0 307 30" width="307" height="30" aria-hidden="true"><polygon points="1,1 306,1 291,15 306,29 1,29 16,15" fill="none" stroke="var(--rule)" stroke-width="1.5"/></svg>
    <span class="banner-label">MINESTRONE SOUP</span>
  </div>
  <p class="line" style="top:499px">Served with Garlic Bread</p>
  <p class="price" style="top:522px">$8</p>

  <!-- Cocktail special -->
  <div class="icon left" style="top:603px;height:88px" role="img" aria-label="Faint line icon of a cocktail glass with citrus slice"></div>
  <div class="icon right" style="top:603px;height:88px" role="img" aria-label="Faint line icon of a cocktail glass with citrus slice"></div>
  <div class="banner" style="top:597px">
    <svg viewBox="0 0 307 30" width="307" height="30" aria-hidden="true"><polygon points="1,1 306,1 291,15 306,29 1,29 16,15" fill="none" stroke="var(--rule)" stroke-width="1.5"/></svg>
    <span class="banner-label">COCKTAIL SPECIAL</span>
  </div>
  <p class="line caps" style="top:638px">Passionista</p>
  <p class="line" style="top:661px">Vodka, Passionfruit Pulp, Mango Puree</p>
  <p class="line" style="top:681px">Top up with Ginger &amp; Lemon Kombucha</p>
  <p class="price" style="top:703px">$17</p>

  <!-- Craft beer special -->
  <div class="icon left" style="top:777px;height:84px" role="img" aria-label="Faint line icon of a bottle and glass"></div>
  <div class="icon right" style="top:777px;height:84px" role="img" aria-label="Faint line icon of a bottle and glass"></div>
  <div class="banner" style="top:771px">
    <svg viewBox="0 0 307 30" width="307" height="30" aria-hidden="true"><polygon points="1,1 306,1 291,15 306,29 1,29 16,15" fill="none" stroke="var(--rule)" stroke-width="1.5"/></svg>
    <span class="banner-label">CRAFT BEER SPECIAL</span>
  </div>
  <p class="line caps" style="top:814px">Crooked Gecko</p>
  <p class="line caps" style="top:834px">Mango Burst</p>
  <p class="line" style="top:853px">Tropical Pale Ale</p>
  <p class="line" style="top:871px">4.8% Alc.</p>
  <p class="price" style="top:901px">$10</p>

  <div class="brand-block">
    <span>SALT MEADOW</span>
    <span>CAFE</span>
  </div>
</body>
</html>
```